Existing Website Requiring new Pages

I have an existing word press website that was built using elementor.
Website: www.tallowcrestcare.com.au
I require the Vacancies page (https://www.tallowcrestcare.com.au/vacancies/) to be modified to display our new properties along with minor tweaks to how the information is presented.
The vacancies to be displayed are the exactly the same as those that are located on the homepage of QMR website (https://qmr.org.au/)
The new pages that link off the Vacancies tab will require custom design.
There are roughly 8 pages/properties to be incorporated. i wish for the design to be very similar to that displayed in the following link; https://www.polunda.com.au/vacancies/merrylands
Along with this the back end has not been updated for the last 3 years so it also requires some maintenance.
Website is in the disability industry and the custom pages will display information relative to Property Vacancies.
I have attached a ZIP file with some design guides, the information for each of the properties (which will need to be modified to show our business name Tallowcrest Care) and the example of how it is to look based off the Polunda website.
If you guys have any suggestions or ideas on how to make this more presentable or possible i'm open to your ideas.
Target Market(s)
People looking for SDA properties custom built for people with a disability
Industry/Entity Type
Disability
Coding
Coded - Design and coding required
Number of Pages Required
5+ page

```html
<!DOCTYPE html>
<html lang="en">
<head>
<meta charset="utf-8">
<title>Vacancies | Tallowcrest Care</title>
<link rel="stylesheet" href="https://fonts.googleapis.com/css2?family=Montserrat:wght@400;500;600;700&display=swap">
<style>
:root{
  --pink:#e6479a;
  --orange:#fbb15e;
  --ink:#1b1b1b;
  --text:#555a60;
  --muted:#8a8f95;
  --rule:#e4e4e4;
  --blue:#2a9fe0;
  --bar:#1f1f1f;
  --white:#ffffff;
}
*{box-sizing:border-box;margin:0;padding:0}
html,body{width:1200px;height:2768px;overflow:hidden;background:var(--white)}
body{position:relative;font-family:"Montserrat",sans-serif;color:var(--ink)}
.abs{position:absolute}

/* header */
.site-header{position:absolute;left:0;top:0;width:1200px;height:128px;background:var(--white)}
.brand{position:absolute;left:115px;top:44px;display:flex;align-items:center;gap:8px;font-size:21px;font-weight:600;color:var(--pink)}
.brand .dot{width:16px;height:16px;border-radius:50%;background:var(--orange)}
.main-nav{position:absolute;top:59px;left:555px;display:flex;gap:0;font-size:11px;font-weight:600;letter-spacing:.6px}
.main-nav a{position:absolute;white-space:nowrap;color:#333;text-decoration:none}
.main-nav a.active{color:#f0873e}

/* hero */
.hero{position:absolute;left:0;top:128px;width:1200px;height:566px;overflow:hidden}
.hero-photo{position:absolute;inset:0;background:linear-gradient(100deg,#7fa1c8 0%,#c59aa3 28%,#b9b39b 50%,#d6d0c0 70%,#c4c7b3 100%)}
.hero-title{position:absolute;left:0;right:0;top:192px;text-align:center;font-size:52px;font-weight:600;color:var(--ink);letter-spacing:1px}
.hero-wave{position:absolute;left:0;bottom:0}

/* cards */
.vacancy{position:absolute;width:302px;height:314px}
.vacancy .photo{position:absolute;left:0;top:0;width:302px;height:228px;border:5px solid #fff;border-radius:14px;box-shadow:0 2px 8px rgba(0,0,0,.18)}
.vacancy .label{position:absolute;left:20px;top:202px;width:261px;height:111px;background:#fff;border-radius:14px;box-shadow:0 4px 14px rgba(0,0,0,.12);text-align:center;padding-top:28px}
.vacancy h3{font-size:20px;font-weight:600;color:var(--ink);letter-spacing:.3px}
.vacancy p{font-size:16px;color:var(--text);margin-top:12px}
.vacancy.featured .photo{border-color:var(--pink)}
.vacancy.featured .label{background:var(--pink)}
.vacancy.featured h3,.vacancy.featured p{color:#fff}

/* contact band */
.contact-band{position:absolute;left:0;top:1880px;width:1200px;height:488px;overflow:hidden}
.contact-photo{position:absolute;inset:0;background:linear-gradient(110deg,#3a342f 0%,#4a3f36 35%,#5c564f 60%,#6d6760 100%)}
.contact-band h2{position:absolute;left:0;right:0;top:155px;text-align:center;font-size:54px;font-weight:600;color:#fff}
.contact-band .lead{position:absolute;left:290px;width:620px;top:230px;text-align:center;font-size:14.5px;line-height:24px;color:#fff}
.btn{position:absolute;left:511px;top:337px;width:178px;height:41px;background:var(--pink);color:#fff;font-size:15px;font-weight:600;text-align:center;line-height:41px;text-decoration:none}

/* footer */
.site-footer{position:absolute;left:0;top:2368px;width:1200px;height:322px}
.footer-brand{position:absolute;left:70px;top:100px;display:flex;align-items:center;gap:8px;font-size:22px;font-weight:600;color:var(--pink)}
.footer-brand .dot{width:16px;height:16px;border-radius:50%;background:var(--orange)}
.footer-contact{position:absolute;left:70px;top:212px;font-size:14px;color:var(--text);list-style:none}
.footer-contact li{display:flex;align-items:center;gap:9px;height:24px}
.footer-contact svg{width:16px;height:16px}
.social{position:absolute;left:513px;top:55px;list-style:none}
.social li{width:36px;height:36px;border-radius:50%;margin-bottom:9px}
.footer-col{position:absolute;top:46px;width:246px}
.footer-col h4{font-size:15px;font-weight:500;color:var(--ink);border-left:3px solid var(--blue);padding-left:14px;height:16px;line-height:16px;letter-spacing:.3px;margin-bottom:16px}
.footer-col ul{list-style:none;border-top:1px solid var(--rule)}
.footer-col li{font-size:14px;color:var(--muted);line-height:24px;padding:6px 0;border-bottom:1px solid var(--rule)}
.legal{position:absolute;left:0;top:2690px;width:1200px;height:78px;background:var(--bar);color:#bbb;font-size:11px;text-align:center;line-height:78px}
.to-top{position:absolute;right:14px;top:20px;width:36px;height:36px;background:#111;display:flex;align-items:center;justify-content:center}
</style>
</head>
<body>

<header class="site-header">
  <div class="brand"><span class="dot"></span>Tallowcrest Care</div>
  <nav class="main-nav">
    <a style="left:0">HOME</a>
    <a style="left:62px">ABOUT US</a>
    <a class="active" style="left:148px">WHAT WE DO ⌄</a>
    <a style="left:272px">REFERRALS</a>
    <a style="left:366px">FEEDBACK</a>
    <a style="left:456px">CONTACT US</a>
  </nav>
</header>

<section class="hero">
  <div class="hero-photo" role="img" aria-label="Carer walking arm in arm with an elderly woman in a garden"></div>
  <h1 class="hero-title">VACANCIES</h1>
  <svg class="hero-wave" width="1200" height="200" viewBox="0 0 1200 200">
    <path d="M0 140 C150 235 330 200 480 150 C700 80 900 20 1060 30 C1130 35 1175 60 1200 80 L1200 200 L0 200 Z" fill="var(--orange)"/>
    <path d="M0 140 C150 240 330 210 480 165 C700 100 900 50 1060 60 C1130 65 1175 95 1200 118 L1200 200 L0 200 Z" fill="#fff"/>
  </svg>
</section>

<main>
  <article class="vacancy" style="left:113px;top:788px"><div class="photo" role="img" aria-label="Penrith home exterior" style="background:linear-gradient(#dfe3e6 45%,#6f7a5e)"></div><div class="label"><h3>PENRITH</h3><p>4 Bedroom SIL Home</p></div></article>
  <article class="vacancy" style="left:449px;top:788px"><div class="photo" role="img" aria-label="Mount Druitt brick home" style="background:linear-gradient(#a8c8e6 20%,#9a6a50 45%,#5c8a3a 75%,#7aa045)"></div><div class="label"><h3>MOUNT DRUITT</h3><p>4 Bedroom SIL Home</p></div></article>
  <article class="vacancy" style="left:786px;top:788px"><div class="photo" role="img" aria-label="Casula home exterior" style="background:linear-gradient(#79b4ea 35%,#d8c9a0 55%,#b8aa8a)"></div><div class="label"><h3>CASULA</h3><p>4 Bedroom SIL Home</p></div></article>

  <article class="vacancy" style="left:113px;top:1138px"><div class="photo" role="img" aria-label="Eastwood cottage exterior" style="background:linear-gradient(#8fb6dc 10%,#cdbfa8 40%,#b9a58e)"></div><div class="label"><h3>EASTWOOD</h3><p>4 Bedroom SIL Home</p></div></article>
  <article class="vacancy featured" style="left:449px;top:1138px"><div class="photo" role="img" aria-label="Baulkham Hills home with garden" style="background:linear-gradient(#6ea6df 30%,#c9c3b8 55%,#5f9a3a 80%)"></div><div class="label"><h3>BAULKHAM HILLS</h3><p>4 Bedroom SIL Home</p></div></article>
  <article class="vacancy" style="left:786px;top:1138px"><div class="photo" role="img" aria-label="Merrylands home exterior" style="background:linear-gradient(#7bb0e6 30%,#b86a44 52%,#6ea842 78%)"></div><div class="label"><h3>MERRYLANDS</h3><p>4 Bedroom SIL Home</p></div></article>

  <article class="vacancy" style="left:281px;top:1488px"><div class="photo" role="img" aria-label="Alexandria two storey home" style="background:linear-gradient(#5a9ce0 20%,#8a7a70 50%,#5d9c2e 75%)"></div><div class="label"><h3>ALEXANDRIA</h3><p>4 Bedroom SIL Home</p></div></article>
  <article class="vacancy" style="left:618px;top:1488px"><div class="photo" role="img" aria-label="Barangaroo weatherboard home" style="background:linear-gradient(#cfd7d3 20%,#8a9a94 50%,#4f7a30 80%)"></div><div class="label"><h3>BARANGAROO</h3><p>4 Bedroom SIL Home</p></div></article>
</main>

<section class="contact-band">
  <div class="contact-photo" role="img" aria-label="Person reading braille at a wooden table"></div>
  <svg class="abs" style="left:0;top:0" width="1200" height="60" viewBox="0 0 1200 60">
    <path d="M0 0 H1200 V10 C1120 30 1060 22 980 34 C880 48 760 30 640 44 C520 56 400 30 300 40 C200 48 100 20 0 28 Z" fill="#fff"/>
  </svg>
  <h2>Get In Touch With Us!</h2>
  <p class="lead">We would love to hear you from from you regarding any concerns, questions or suggestions you may have. Please use the contact us now button to reach the Tallowcrest Care Team.</p>
  <a class="btn">Contact Us Now</a>
</section>

<footer class="site-footer">
  <div class="footer-brand"><span class="dot"></span>Tallowcrest Care</div>
  <ul class="footer-contact">
    <li><svg viewBox="0 0 16 16"><rect x="1.5" y="3.5" width="13" height="9" fill="none" stroke="var(--pink)" stroke-width="1.4"/><path d="M1.5 3.5 L8 9 L14.5 3.5" fill="none" stroke="var(--pink)" stroke-width="1.4"/></svg>Email: info@tallowcrestcare.com.au</li>
    <li><svg viewBox="0 0 16 16"><path d="M3 1.5 L6 1.5 L7 5 L5 6.5 C6 9 7 10 9.5 11 L11 9 L14.5 10 L14.5 13 C14.5 14 13.5 14.8 12.5 14.5 C6.5 13 3 9.5 1.5 3.5 C1.3 2.5 2 1.5 3 1.5 Z" fill="var(--pink)"/></svg>Phone: +61 0400 318 642</li>
    <li><svg viewBox="0 0 16 16"><circle cx="8" cy="8" r="6.5" fill="none" stroke="var(--pink)" stroke-width="1.4"/><path d="M8 4 V8 L10.5 9.5" fill="none" stroke="var(--pink)" stroke-width="1.4"/></svg>Operating Hours: 9AM To 5PM Monday - Friday</li>
  </ul>
  <ul class="social">
    <li style="background:#6b2d86"></li>
    <li style="background:#1877c9"></li>
    <li style="background:#1b1b1b"></li>
    <li style="background:#0a66c2"></li>
  </ul>
  <div class="footer-col" style="left:614px">
    <h4>ACCOMMODATION</h4>
    <ul>
      <li>Supported Independent Living (SIL)</li>
      <li>Specialist Disability Accommodation (SDA)</li>
      <li>Short term Accommodation (Respite)</li>
      <li>Vacancies</li>
    </ul>
  </div>
  <div class="footer-col" style="left:886px">
    <h4>WHAT WE DO</h4>
    <ul>
      <li>In Home Care</li>
      <li>Social &amp; Community Services</li>
      <li>Therapeutic Supports</li>
      <li>Support Coordination</li>
      <li>Home Modifications</li>
    </ul>
  </div>
</footer>

<div class="legal">© Copyright 2024 | Tallowcrest Care | All Rights Reserved.
  <div class="to-top"><svg width="12" height="8" viewBox="0 0 12 8"><path d="M1 7 L6 2 L11 7" fill="none" stroke="#fff" stroke-width="2"/></svg></div>
</div>

</body>
</html>
```